Business card design needed

Family General Practitioner/ Family Physician.
Logo is the logo of the Noble Guild of Family Healers Oceania
http://kpltw.varendo.example/ImageShelf/marks/pages/NGFHO%20mark_jpg.htm
Updates

Project Deadline Extended
Reason: Just a bit more time to make changes and the weekend for me to look at things closely and to choose. Thanks, Orin

Thanks for all the submissions. So many of them are really works of art. Not one of them are not good. The ones that I am eliminating are the ones that I think are not suitable for me personally only, and because if I don't, it makes it very difficult to decide as many of you are also sending me slight variations of a card. I have just decided to choose a second place card too. Can't thank you all enough. Good luck, Orin. P.S - Working today till 10 pm as the card says :-), so probably won't be able to give a feedback till late Saturday night or Sunday morning here in Sydney, Australia. 

Project Deadline Extended
Reason: Just added a second place to the budget and realised that Australia is ahead of the rest of the world in the time zone (only :-) - don't want to offend anyone or start a debate!! ) , so Monday deadline will mean it will be a weekend for the rest of the world. Just wanted to give everyone more time to submit their best, especially since I will be picking a second card too. Can't thank everyone enough for the submissions. P.S - Not keen on photos on the card.

Industry/Entity Type

Business

Contact Information for Business Card

Dr. Orin Halvey M.B.B.S., F.N.G.F.H.O
Family General Practitioner
Address, timings, phone and fax number on the back.

Requirements
Must have
• Timings
Mon 7 am - 7 pm
Tues 7 am - 12 pm
Wed 7 am - 10 pm
Thurs 7 am - 12 pm
Fri 7 am - 8 pm
Sat 8 am - 10 pm
Sun - Off

```html
<!DOCTYPE html>
<html lang="en">
<head>
<meta charset="utf-8">
<title>Dr. Orin Halvey – Business Card</title>
<link rel="stylesheet" href="https://fonts.googleapis.com/css2?family=Great+Vibes&family=Playfair+Display+SC:wght@400&family=Tinos&display=swap">
<style>
  :root {
    --sky: #9ff0fb;
    --paper: #ffffff;
    --royal-blue: #0a1fd0;
    --orange: #f26a1b;
    --orange-bright: #ff5a00;
    --peach: #f7b896;
  }
  html, body {
    margin: 0;
    padding: 0;
    width: 741px;
    height: 1200px;
    overflow: hidden;
    background: var(--paper);
  }
  .card {
    position: relative;
    width: 741px;
    height: 1200px;
    overflow: hidden;
    background: linear-gradient(135deg, var(--sky) 0%, #d4f8fd 28%, var(--paper) 55%);
  }
  .vertical {
    position: absolute;
    margin: 0;
    transform-origin: left top;
    transform: rotate(-90deg);
    white-space: nowrap;
    line-height: 1;
  }
  .doctor-name {
    left: 50px;
    top: 1136px;
    font-family: "Playfair Display SC", "Times New Roman", serif;
    font-weight: 400;
    font-size: 122px;
    color: var(--royal-blue);
  }
  .speciality {
    left: 183px;
    top: 563px;
    font-family: "Tinos", "Times New Roman", serif;
    font-size: 38px;
    letter-spacing: 1px;
    color: var(--orange);
  }
  .credentials {
    left: 183px;
    top: 1136px;
    font-family: "Tinos", "Times New Roman", serif;
    font-size: 34px;
    letter-spacing: 1px;
    color: var(--orange);
  }
  .family-artwork {
    position: absolute;
    left: 276px;
    top: 124px;
    width: 362px;
    height: 348px;
    border-radius: 8px;
    background: linear-gradient(180deg, #eef0f1 0%, #d9dcde 70%, #e6f5dc 100%);
  }
  .tagline-initial {
    position: absolute;
    left: 262px;
    top: 598px;
    font-family: "Great Vibes", cursive;
    font-size: 86px;
    line-height: 1;
    color: var(--peach);
  }
  .tagline-text {
    position: absolute;
    left: 321px;
    top: 620px;
    font-family: "Tinos", "Times New Roman", serif;
    font-size: 36px;
    line-height: 1;
    color: var(--orange);
  }
  .tagline-badge {
    position: absolute;
    left: 577px;
    top: 577px;
    width: 130px;
    height: 130px;
    border-radius: 50%;
    background: var(--orange-bright);
    display: flex;
    align-items: center;
    justify-content: center;
    font-family: "Tinos", "Times New Roman", serif;
    font-size: 34px;
    color: var(--paper);
  }
  .address {
    position: absolute;
    left: 249px;
    top: 1025px;
    margin: 0;
    font-family: "Tinos", "Times New Roman", serif;
    font-style: normal;
    font-size: 32px;
    line-height: 41px;
    color: var(--royal-blue);
  }
</style>
</head>
<body>
  <main class="card">
    <h1 class="vertical doctor-name">Dr. Orin Halvey</h1>
    <p class="vertical speciality">Family General Practitioner</p>
    <p class="vertical credentials">M.B.B.S.. F.N.G.F.H.O</p>

    <div class="family-artwork" role="img" aria-label="Illustration of a family group standing together on grass under the sun"></div>

    <span class="tagline-initial">C</span>
    <span class="tagline-text">aring about your</span>
    <span class="tagline-badge">health</span>

    <address class="address">
      Upper Level, Lantern Court<br>
      Larkspur Galleria Centre<br>
      Fernbrook Rise, NSW 2189
    </address>
  </main>
</body>
</html>
```